Unique Business Card Design

Unique Business Card design for our orthotic and prosthetic company. Our logo is on our website, color is light blue. Unique shape (artificial leg shaped, vertical, etc..) preferred. Logo, business name, individual name and basic demographics needed.

Industry/Entity Type

Business

Contact Information for Business Card

Logo, Industry, Phone # Logo, "Prosthetic & Orthotic Services" Place to add individual name and contact info

Colors
cee9f5

Requirements
Must have
• The icon must be there, placement of "Prosthetic & Orthotic Services" can be moved
Nice to have
• Like the mix of light blue, and a little darker blue. One design included the icons from my website which was a nice touch

```html
<!DOCTYPE html>
<html lang="en">
<head>
<meta charset="utf-8">
<title>Stridewell Inc. Business Card</title>
<link href="https://fonts.googleapis.com/css2?family=Roboto:wght@400;500;700&display=swap" rel="stylesheet">
<style>
  :root {
    --brand-blue: #0b5aa8;
    --brand-blue-light: #1b6db8;
    --sky-blue: #cee9f5;
    --text-grey: #555a60;
    --rule-grey: #dadde1;
    --card-white: #ffffff;
    --backdrop: #e9eef1;
  }
  * { margin: 0; padding: 0; box-sizing: border-box; }
  html, body {
    width: 1200px; height: 1000px; overflow: hidden;
    background: var(--backdrop);
    font-family: "Roboto", Arial, sans-serif;
  }
  .canvas { position: relative; width: 1200px; height: 1000px; }

  .card {
    position: absolute; left: 220px; width: 760px;
    border-radius: 28px; overflow: hidden;
    box-shadow: 0 6px 18px rgba(0,0,0,0.18);
  }
  .card-front {
    top: 50px; height: 433px;
    background: linear-gradient(120deg, var(--brand-blue) 0%, var(--brand-blue) 55%, var(--brand-blue-light) 100%);
  }
  .card-back { top: 524px; height: 436px; background: var(--card-white); }

  .brand { position: absolute; display: flex; align-items: center; }
  .brand-mark { border-radius: 50%; flex: none; }
  .brand-text { display: flex; flex-direction: column; }
  .brand-name { font-weight: 500; white-space: nowrap; }
  .brand-tagline {
    font-size: 13px; font-weight: 500; letter-spacing: 2.6px;
    color: var(--sky-blue); margin-top: 6px; white-space: nowrap;
  }

  .card-front .brand { left: 136px; top: 161px; }
  .card-front .brand-mark { width: 114px; height: 114px; background: var(--card-white); margin-right: 14px; }
  .card-front .brand-name { font-size: 41px; letter-spacing: 0.6px; color: var(--card-white); line-height: 44px; }

  .card-back .brand { left: 357px; top: 40px; }
  .card-back .brand-mark { width: 84px; height: 84px; background: var(--brand-blue); margin-right: 10px; }
  .card-back .brand-name { font-size: 30px; letter-spacing: 0.6px; color: var(--brand-blue); }

  .side-tab {
    position: absolute; left: 0; top: 211px; width: 10px; height: 37px;
    background: var(--brand-blue); border-radius: 0 4px 4px 0;
  }
  .person { position: absolute; left: 42px; top: 206px; }
  .person-name { font-size: 22px; font-weight: 700; color: var(--brand-blue); line-height: 28px; letter-spacing: 0.3px; }
  .person-title { font-size: 17px; color: var(--text-grey); line-height: 20px; letter-spacing: 0.4px; }

  .divider { position: absolute; left: 42px; right: 43px; top: 265px; height: 1px; background: var(--rule-grey); }

  .contact-list { position: absolute; left: 42px; top: 282px; list-style: none; }
  .contact-list li {
    display: flex; align-items: center; height: 24px;
    font-size: 17px; color: var(--text-grey); letter-spacing: 0.5px;
  }
  .contact-list svg { width: 13px; height: 13px; margin-right: 8px; fill: var(--brand-blue); }

  .address { position: absolute; right: 43px; top: 285px; text-align: right; font-size: 17px; line-height: 24px; color: var(--text-grey); letter-spacing: 0.5px; }
  .address .company { color: var(--brand-blue); }
  .address .web { margin-top: 6px; }
  .address .web span { color: var(--brand-blue); }

  .footer-rule { position: absolute; left: 0; right: 0; top: 414px; height: 2px; background: var(--sky-blue); }
  .footer-band { position: absolute; left: 0; right: 0; top: 419px; height: 17px; background: var(--brand-blue); }
</style>
</head>
<body>
<div class="canvas">
  <section class="card card-front">
    <div class="brand">
      <div class="brand-mark"></div>
      <div class="brand-text">
        <div class="brand-name">STRIDEWELL INC.</div>
        <div class="brand-tagline">PROSTHETIC &amp; ORTHOTIC SERVICES</div>
      </div>
    </div>
  </section>

  <section class="card card-back">
    <div class="brand">
      <div class="brand-mark"></div>
      <div class="brand-name">STRIDEWELL INC.</div>
    </div>

    <div class="side-tab"></div>
    <div class="person">
      <div class="person-name">Mirela Tanvoss</div>
      <div class="person-title">CO LPO</div>
    </div>
    <div class="divider"></div>

    <ul class="contact-list">
      <li><svg viewBox="0 0 16 16"><path d="M4 0h8a1.5 1.5 0 0 1 1.5 1.5v13A1.5 1.5 0 0 1 12 16H4a1.5 1.5 0 0 1-1.5-1.5v-13A1.5 1.5 0 0 1 4 0zm0 2v10.5h8V2zm4 11.3a.9.9 0 1 0 0 1.8.9.9 0 0 0 0-1.8z"/></svg>845-5550142</li>
      <li><svg viewBox="0 0 16 16"><path d="M3.6 1l2.6 3.3-1.5 1.6c.9 2 2.6 3.8 4.6 4.9l1.6-1.5L14.2 12l-1.6 2.6C6.6 14.3 1.9 9.4 1.4 3.2z"/></svg>(718) 555-0170</li>
      <li><svg viewBox="0 0 16 16"><path d="M4 1h8v4H4zM1 6h14v6h-3v3H4v-3H1zm4 4v3h6v-3z"/></svg>(718) 555-0139</li>
      <li><svg viewBox="0 0 16 16"><path d="M0 3h16v1.2L8 9 0 4.2zM0 6l8 4.8L16 6v7H0z"/></svg>Mtanvoss@stridewellinc.com</li>
    </ul>

    <div class="address">
      <div class="company">STRIDEWELL INC.</div>
      <div>2260 Harbor Lane</div>
      <div>Brooklyn, NY 11299</div>
      <div class="web">www.<span>stridewellinc</span>.net</div>
    </div>

    <div class="footer-rule"></div>
    <div class="footer-band"></div>
  </section>
</div>
</body>
</html>
```